Recruiting Firm Need Professional, Modern Tri-Fold Brochure for their United States Based Business

-We need a professional, modern TRI-FOLD brochure design that can help generate business for our recruiting firm. We need an impressive brochure.
- Please use the about us website content and attached website content. Website: www.morvellstaffingpartners.example
- Please use logo files attached.
- Please note: This brochure will be the starting point for an upgraded website design so we are NOT looking for a brochure to look like our current website.
- We want potential clients to want to do business with us just based on the brochure look and feel alone.

Target Market(s)

small, medium, and large companies who need administrative, human resources, and accounting talent

Industry/Entity Type

Professional Service

Font styles to use
Serif

Requirements
Must have
• - Professional, Modern TRI-FOLD Brochure Design for United States Based Company
• - Please show diverse group of professionals pictures similar to the ones on our website. One pic must include an African American female and one pic must include an African male. Or both an African American female and male can be include in the group of other races. But All the group photos must be diverse in race and include both male and female.
• - Please show pics of one business professional too
• a diverse group photo would be nice on the front cover...so we can show diversity and inclusion from the start
Should not have
• - Please DO NOT use the same pictures on our website.

```html
<!DOCTYPE html>
<html lang="en">
<head>
<meta charset="utf-8">
<title>Morvell Staffing Partners – Tri-Fold Brochure</title>
<link href="https://fonts.googleapis.com/css2?family=Cinzel:wght@500&family=Open+Sans:wght@300;400&display=swap" rel="stylesheet">
<style>
  :root {
    --backdrop: #e9e9e9;
    --brand-red: #b20404;
    --brand-red-light: #c81a1a;
    --band-dark: #2b2b2b;
    --paper: #ffffff;
    --ink: #222222;
    --on-red: #ffffff;
    --mark-grey: #4a4a4a;
  }
  * { box-sizing: border-box; margin: 0; padding: 0; }
  html, body { width: 1200px; height: 923px; overflow: hidden; background: var(--backdrop); }
  .brochure {
    position: absolute; left: 39px; top: 64px;
    width: 1122px; height: 794px;
    background: var(--paper); overflow: hidden;
    box-shadow: 0 4px 18px rgba(0,0,0,.25);
    font-family: "Open Sans", sans-serif; font-weight: 300;
  }
  .panel-photo { position: absolute; top: 0; height: 600px; width: 374px; }
  .photo-receptionist { left: 0; background: linear-gradient(160deg, #dfe0e1 0%, #c9cacb 45%, #8d8c8c 75%, #3a3a3c 100%); }
  .photo-meeting-faded { left: 374px; background: linear-gradient(180deg, #f7f7f7 0%, #efefef 50%, #f4f4f4 100%); }
  .photo-team { left: 748px; width: 374px; background: linear-gradient(150deg, #e6e6e3 0%, #bfc4c9 35%, #7f858d 60%, #d8e0e6 100%); }
  .panel-divider { position: absolute; top: 0; bottom: 0; width: 1px; background: rgba(0,0,0,.06); }
  .posting-box { position: absolute; left: 612px; top: 39px; width: 93px; height: 96px; background: #ececec; border: 1px solid #d8d8d8; }
  .posting-title { position: absolute; left: 374px; width: 374px; top: 214px; text-align: center; font-size: 24px; color: var(--ink); font-weight: 300; }
  .sweep { position: absolute; left: 0; top: 0; width: 1122px; height: 794px; }
  .contact { position: absolute; color: var(--on-red); text-align: center; font-size: 17px; }
  .contact-line { display: flex; align-items: center; justify-content: center; gap: 8px; white-space: nowrap; }
  .contact-line svg { flex: none; }
  .left-contact { left: 0; width: 374px; top: 714px; }
  .left-contact .phone { font-size: 25px; margin-bottom: 10px; }
  .middle-contact { left: 374px; width: 374px; top: 693px; }
  .middle-contact .contact-line { margin-bottom: 7px; }
  .brand { position: absolute; text-align: center; color: var(--on-red); }
  .brand-square { width: 52px; height: 52px; background: var(--mark-grey); margin: 0 auto 10px; }
  .brand-name { font-family: "Cinzel", serif; font-weight: 500; letter-spacing: .5px; line-height: 1.05; }
  .brand-rule { height: 1px; background: rgba(255,255,255,.35); margin: 12px auto 0; }
  .middle-brand { left: 374px; width: 374px; top: 570px; }
  .middle-brand .brand-name { font-size: 17px; }
  .middle-brand .brand-rule { width: 210px; }
  .cover-brand { left: 748px; width: 374px; top: 573px; }
  .cover-brand .brand-name { font-size: 21px; }
  .cover-brand .brand-rule { width: 210px; margin-top: 12px; }
  .tagline { margin-top: 14px; font-size: 17px; font-weight: 400; line-height: 1.42; }
</style>
</head>
<body>
<div class="brochure">
  <div class="panel-photo photo-receptionist" role="img" aria-label="Photo of a business professional on the phone at her desk"></div>
  <div class="panel-photo photo-meeting-faded" role="img" aria-label="Faded photo of colleagues meeting, used as backdrop"></div>
  <div class="panel-photo photo-team" role="img" aria-label="Photo of a diverse team of professionals working around a table"></div>
  <div class="panel-divider" style="left:374px"></div>
  <div class="panel-divider" style="left:748px"></div>

  <div class="posting-box"></div>
  <p class="posting-title">Posting Details Here</p>

  <svg class="sweep" viewBox="0 0 1122 794" aria-hidden="true">
    <defs>
      <linearGradient id="redGlow" x1="0" y1="0" x2="0" y2="1">
        <stop offset="0" stop-color="#c20808"/>
        <stop offset="1" stop-color="#a80202"/>
      </linearGradient>
    </defs>
    <path d="M0,600 Q540,350 1122,600 L1122,794 L0,794 Z" fill="#ffffff"/>
    <path d="M0,625 Q540,390 1122,596 L1122,794 L0,794 Z" fill="var(--band-dark)"/>
    <path d="M0,660 Q540,420 1122,598 L1122,794 L0,794 Z" fill="#ffffff"/>
    <path d="M0,690 Q540,440 1122,600 L1122,794 L0,794 Z" fill="url(#redGlow)"/>
    <rect x="16" y="696" width="346" height="92" fill="#ffffff" opacity=".05"/>
    <rect x="760" y="620" width="346" height="160" fill="#ffffff" opacity=".05"/>
    <line x1="374" y1="520" x2="374" y2="794" stroke="#000" stroke-opacity=".08"/>
    <line x1="748" y1="520" x2="748" y2="794" stroke="#000" stroke-opacity=".08"/>
  </svg>

  <div class="contact left-contact">
    <p class="contact-line phone">
      <svg width="22" height="22" viewBox="0 0 22 22"><circle cx="11" cy="11" r="9.5" fill="none" stroke="#fff" stroke-width="1.6"/><path d="M8 6.5l1.6 2.2-1 1.1c.7 1.4 1.7 2.4 3 3l1.1-1 2.2 1.6-1 1.6c-3.4-.3-6.2-3.1-6.6-6.5z" fill="#fff"/></svg>
      555-014-0627
    </p>
    <p class="contact-line">
      <svg width="15" height="15" viewBox="0 0 16 16"><circle cx="8" cy="8" r="6.8" fill="none" stroke="#fff" stroke-width="1.1"/><ellipse cx="8" cy="8" rx="3" ry="6.8" fill="none" stroke="#fff" stroke-width="1.1"/><line x1="1.2" y1="8" x2="14.8" y2="8" stroke="#fff" stroke-width="1.1"/></svg>
      www.morvellstaffingpartners.example
    </p>
  </div>

  <div class="brand middle-brand">
    <div class="brand-square"></div>
    <p class="brand-name">MORVELL STAFFING PARTNERS</p>
    <div class="brand-rule"></div>
  </div>
  <div class="contact middle-contact">
    <p class="contact-line">
      <svg width="15" height="15" viewBox="0 0 22 22"><circle cx="11" cy="11" r="9.5" fill="none" stroke="#fff" stroke-width="1.8"/><path d="M8 6.5l1.6 2.2-1 1.1c.7 1.4 1.7 2.4 3 3l1.1-1 2.2 1.6-1 1.6c-3.4-.3-6.2-3.1-6.6-6.5z" fill="#fff"/></svg>
      555-014-0627
    </p>
    <p class="contact-line">
      <svg width="14" height="10" viewBox="0 0 14 10"><rect x=".6" y=".6" width="12.8" height="8.8" fill="none" stroke="#fff" stroke-width="1.1"/><path d="M.6 .6L7 5.6 13.4 .6" fill="none" stroke="#fff" stroke-width="1.1"/></svg>
      info@morvellstaffingpartners.example
    </p>
    <p class="contact-line">
      <svg width="15" height="15" viewBox="0 0 16 16"><circle cx="8" cy="8" r="6.8" fill="none" stroke="#fff" stroke-width="1.1"/><ellipse cx="8" cy="8" rx="3" ry="6.8" fill="none" stroke="#fff" stroke-width="1.1"/><line x1="1.2" y1="8" x2="14.8" y2="8" stroke="#fff" stroke-width="1.1"/></svg>
      www.morvellstaffingpartners.example
    </p>
  </div>

  <div class="brand cover-brand">
    <div class="brand-square"></div>
    <p class="brand-name">MORVELL STAFFING PARTNERS</p>
    <div class="brand-rule"></div>
    <p class="tagline">Providing Top-Notch<br>Administrative, Human Resources,<br>and Accounting Talent</p>
  </div>
</div>
</body>
</html>
```